Online Shop - Website Design for up an coming art studio

We require a fully functional website design - not just design - but complete coded online shop website please, which should be a word press style frame work to allow ease up updating the site in the future. The website will sell art work from up and coming artists. The business is called "Brindle Harbor Studios". I have attached our logo to allow the submitted designs to tie in with this.

Industry/Entity Type

Shop

Coding

Coded - Design and coding required

Number of Pages Required

1 page

Colors

Designer to choose colors to be used in the design.

Requirements
Must have
• The website design must incorporate and fully functional online eCommerce shop feature.

```html
<!DOCTYPE html>
<html lang="en">
<head>
<meta charset="utf-8">
<title>Brindle Harbor Studios – Art Shop</title>
<link href="https://fonts.googleapis.com/css2?family=Lato:wght@400;700;900&display=swap" rel="stylesheet">
<style>
:root{
  --red:#d9184b;
  --yellow:#f3e63a;
  --gold:#e8c330;
  --orange:#f39321;
  --tan:#c2b092;
  --black:#000;
  --ink:#222;
  --grey:#666;
  --light:#efeff0;
  --price:#f08a1c;
  --green:#8cc63f;
  --blue:#27a6d8;
}
*{box-sizing:border-box;margin:0;padding:0}
html,body{width:1200px;height:2639px;overflow:hidden}
body{font-family:"Lato",sans-serif;color:var(--ink);background:#fff;position:relative}
.abs{position:absolute}
/* header */
.header{position:absolute;left:0;top:0;width:1200px;height:140px;background:#fff}
.brand{left:132px;top:16px;width:176px;text-align:center}
.brand-dot{width:66px;height:66px;border-radius:50%;background:var(--ink);margin:0 auto 10px}
.brand-name{font-size:17px;font-weight:700;letter-spacing:1px;color:var(--ink);line-height:1.1;white-space:nowrap}
.brand-sub{font-size:7px;font-weight:700;letter-spacing:4px;color:var(--ink);margin-top:2px}
.contact{top:24px;left:712px;font-size:11px;color:var(--ink);display:flex;gap:22px;align-items:center}
.contact span{display:flex;gap:6px;align-items:center}
.login{left:1000px;top:18px;width:70px;height:30px;border:1px solid #bbb;font-size:10px;display:flex;align-items:center;justify-content:center;gap:5px}
.search{left:716px;top:72px;width:354px;height:41px;border:1px solid #333;display:flex}
.search-field{flex:1;font-size:9px;color:#666;padding-left:18px;display:flex;align-items:center}
.search-btn{width:50px;background:var(--yellow);display:flex;align-items:center;justify-content:center}
/* nav */
.nav{left:0;top:140px;width:1200px;height:37px;background:var(--black)}
.nav a{position:absolute;top:0;height:37px;line-height:37px;color:#fff;font-size:10px;font-weight:700;text-decoration:none}
.nav .active{background:var(--red);width:78px;text-align:center}
.nav .cart{background:var(--yellow);color:var(--black);width:118px;text-align:center}
/* hero */
.hero{left:0;top:177px;width:1200px;height:538px;background:linear-gradient(120deg,#8f9f78,#a8b58e 45%,#7d8c66)}
.hero-art{position:absolute;inset:0}
.hero-title{position:absolute;left:0;width:1200px;top:370px;text-align:center;font-size:36px;font-weight:900;color:var(--yellow);letter-spacing:1px}
.btn{display:inline-block;background:var(--red);color:#fff;font-weight:700;text-transform:uppercase}
.hero-btn{position:absolute;left:523px;top:438px;width:124px;height:30px;line-height:30px;text-align:center;font-size:13px}
/* section titles */
.h2{font-size:23px;font-weight:900;color:var(--red);text-transform:uppercase;line-height:1.1}
.arrows{display:flex;gap:16px;color:#555;font-size:22px}
/* artwork */
.artwork{left:0;top:715px;width:1200px;height:520px;background:var(--light)}
.card{position:absolute;top:105px;width:218px}
.frame{width:218px;height:276px;border:9px solid #c7c7c9;background:#fff;padding:8px}
.frame div{width:100%;height:100%}
.card-title{margin-top:28px;font-size:11px;color:#333}
.old{margin-top:10px;font-size:11px;color:#999;text-decoration:line-through}
.new{font-size:13px;color:var(--price);font-weight:700}
.buy{position:absolute;right:0;top:336px;width:54px;height:22px;line-height:22px;text-align:center;font-size:9px}
/* featured */
.featured{left:0;top:1235px;width:1200px;height:660px;background:#fff}
.promo-box{position:absolute;width:212px;height:110px;background:var(--gold);padding:16px 20px;font-size:14px;color:var(--ink);line-height:1.45}
.promo-box .btn{font-size:10px;padding:6px 10px;margin-top:6px}
.panel{position:absolute;top:117px;height:475px}
.panel-title{font-size:34px;font-weight:900;color:#fff;line-height:1.08}
.panel-btn{font-size:10px;height:24px;line-height:24px;text-align:center}
/* testimonials */
.testimonials{left:0;top:1895px;width:1200px;height:268px;background:var(--light)}
.quote{position:absolute;top:50px;width:170px;font-size:11px;line-height:1.6;color:#444}
.stars{color:var(--blue);font-size:13px;letter-spacing:2px;margin-top:14px}
.who{font-size:9px;font-weight:700;margin-top:26px}
.divider{position:absolute;top:40px;width:1px;height:186px;background:#d3d3d3}
.view-all{background:var(--green);color:#fff;font-size:9px;font-weight:700;width:80px;height:24px;line-height:24px;text-align:center}
/* footer */
.footer{left:0;top:2163px;width:1200px;height:476px;background:var(--black);color:#fff}
.foot-brand{left:132px;top:48px;width:213px;text-align:center}
.foot-brand .brand-dot{background:#fff;width:90px;height:90px;margin-bottom:14px}
.foot-brand .brand-name{color:#fff;font-size:20px}
.foot-brand .brand-sub{color:#fff;font-size:8px}
.menu-label{left:438px;top:54px;font-size:10px;font-weight:700}
.address{left:438px;top:96px;font-size:12px;line-height:2;color:#aaa}
.map{left:683px;top:51px;width:387px;height:273px;background:linear-gradient(135deg,#e6e4df,#d9d7d1)}
.news-label{left:132px;top:286px;font-size:10px;font-weight:700}
.news{left:287px;top:273px;width:338px;height:44px;display:flex;background:#fff}
.news-field{flex:1;color:#555;font-size:11px;display:flex;align-items:center;gap:10px;padding-left:16px}
.news-btn{width:102px;background:var(--green);color:var(--ink);font-size:17px;font-weight:700;display:flex;align-items:center;justify-content:center;border:2px solid #fff}
.foot-line{left:132px;top:371px;width:938px;height:1px;background:#333}
.follow{left:132px;top:415px;font-size:10px;font-weight:700;display:flex;align-items:center;gap:18px}
.social{display:flex;gap:9px}
.social span{width:28px;height:28px;border-radius:50%}
.links{left:371px;top:417px;font-size:10px;color:#999}
.copy{left:878px;top:417px;font-size:9px;color:#999}
</style>
</head>
<body>

<header class="header">
  <div class="abs brand"><div class="brand-dot"></div><div class="brand-name">BRINDLE HARBOR</div><div class="brand-sub">STUDIOS</div></div>
  <div class="abs contact">
    <span><svg width="10" height="8" viewBox="0 0 10 8"><rect width="10" height="8" fill="#222"/><path d="M0 0l5 4 5-4" stroke="#fff" fill="none"/></svg>info@brindleharbor.com</span>
    <span><svg width="10" height="10" viewBox="0 0 10 10"><path d="M2 0l2 3-1 1c1 2 2 3 3 3l1-1 3 2-1 2C4 10 0 6 0 1z" fill="#222"/></svg>(555) 014.2290</span>
  </div>
  <div class="abs login"><svg width="8" height="9" viewBox="0 0 8 9"><rect y="4" width="8" height="5" fill="#222"/><path d="M2 4V2.5a2 2 0 014 0V4" stroke="#222" fill="none"/></svg>LOGIN</div>
  <div class="abs search">
    <div class="search-field">SEARCH ALL ARTWORK</div>
    <div class="search-btn"><svg width="16" height="16" viewBox="0 0 16 16"><circle cx="6.5" cy="6.5" r="5" stroke="#222" stroke-width="2.2" fill="none"/><path d="M10 10l5 5" stroke="#222" stroke-width="2.5"/></svg></div>
  </div>
</header>

<nav class="abs nav">
  <a class="active" style="left:116px">HOME</a>
  <a style="left:245px">ABOUT US</a>
  <a style="left:365px">BUY ART</a>
  <a style="left:475px">FEATURES</a>
  <a style="left:584px">ARTISTS</a>
  <a style="left:705px">BLOGS</a>
  <a style="left:820px">CONTACT US</a>
  <a class="cart" style="left:952px">&#128722;&#xFE0E; MY CART (0)</a>
</nav>

<section class="abs hero">
  <div class="hero-art" role="img" aria-label="Gallery wall of framed classical portrait paintings with a large gilded central frame"></div>
  <div class="hero-title">ARTWORK &nbsp;COLLECTIONS</div>
  <a class="btn hero-btn">SHOP NOW &#9656;</a>
</section>

<section class="abs artwork">
  <h2 class="abs h2" style="left:132px;top:44px">Artwork</h2>
  <div class="abs arrows" style="left:1026px;top:38px"><span>&#8249;</span><span>&#8250;</span></div>

  <div class="card" style="left:132px">
    <div class="frame"><div role="img" aria-label="Mural of a woman with flowing blue hair" style="background:linear-gradient(160deg,#8aa3c4,#3e5f8e)"></div></div>
    <div class="card-title">LOREM IPSUM IS SIMPL</div><div class="old">$450.00</div><div class="new">$359.00</div><a class="btn buy">BUY NOW</a>
  </div>
  <div class="card" style="left:370px">
    <div class="frame"><div role="img" aria-label="Photograph of a figure in a red sari at a carved doorway" style="background:linear-gradient(160deg,#d8c7a8,#a9543a)"></div></div>
    <div class="card-title">LOREM IPSUM IS SIMPL</div><div class="old">$450.00</div><div class="new">$359.00</div><a class="btn buy">BUY NOW</a>
  </div>
  <div class="card" style="left:610px">
    <div class="frame"><div role="img" aria-label="Close-up photograph of darts in a dartboard" style="background:linear-gradient(160deg,#4a4a48,#2f2f2e)"></div></div>
    <div class="card-title">LOREM IPSUM IS SIMPL</div><div class="old">$450.00</div><div class="new">$359.00</div><a class="btn buy">BUY NOW</a>
  </div>
  <div class="card" style="left:852px">
    <div class="frame"><div role="img" aria-label="Colourful pop-art face painting" style="background:linear-gradient(135deg,#e0323b,#2b58c8 55%,#7b2fa6)"></div></div>
    <div class="card-title">LOREM IPSUM IS SIMPL</div><div class="old">$450.00</div><div class="new">$359.00</div><a class="btn buy">BUY NOW</a>
  </div>
</section>

<section class="abs featured">
  <h2 class="abs h2" style="left:131px;top:62px">Featured Collections</h2>
  <div class="abs arrows" style="left:548px;top:64px"><span>&#8249;</span><span>&#8250;</span></div>

  <div class="abs" role="img" aria-label="Illustration of a traveller beneath a red tree at sunset" style="left:132px;top:117px;width:458px;height:341px;background:linear-gradient(160deg,#5b7fc4,#e37a4a 45%,#f2c84b 75%,#a45a2a)"></div>
  <div class="promo-box" style="left:374px;top:345px">LOREM IPSUM IS SIMPLY<br>DUMMY TEXT OF<br><a class="btn">BUY NOW</a></div>
  <div class="abs" role="img" aria-label="Wall of framed artworks" style="left:132px;top:469px;width:146px;height:123px;background:linear-gradient(135deg,#b04a38,#e6d6c4)"></div>
  <div class="abs" role="img" aria-label="Sketch of a city street with a red tree" style="left:289px;top:469px;width:146px;height:123px;background:linear-gradient(135deg,#d02a2a,#9a9a9a 60%,#eee)"></div>
  <div class="abs" role="img" aria-label="Tropical flower pattern print" style="left:444px;top:469px;width:146px;height:123px;background:linear-gradient(135deg,#f08aa0,#3ab0a0 60%,#f2d26a)"></div>

  <div class="panel" style="left:600px;width:231px;background:var(--orange)">
    <div class="panel-title abs" style="left:27px;top:18px">CUSTOM<br>ARTWORK</div>
    <div class="abs" style="left:30px;top:105px;font-size:10px;font-weight:700">LOREM IPSUM IS SIMPL</div>
    <a class="btn panel-btn abs" style="left:32px;top:130px;width:152px">VIEW ALL COLLECTIONS</a>
    <div class="abs" role="img" aria-label="Collage of framed portrait artworks" style="left:52px;top:170px;width:164px;height:305px;background:linear-gradient(160deg,#fff 0,#c44 25%,#333 55%,#9cc 80%)"></div>
  </div>

  <div class="panel" style="left:840px;width:230px;background:var(--tan)">
    <div class="panel-title abs" style="left:0;width:230px;text-align:center;top:20px">10%<br>OFFER</div>
    <a class="btn panel-btn abs" style="left:38px;top:130px;width:152px">SPECIAL OFFERS</a>
    <div class="abs" role="img" aria-label="Framed nature poster with mountains and lake" style="left:14px;top:176px;width:198px;height:260px;background:#1a1a1a;padding:12px"><div style="width:100%;height:100%;background:linear-gradient(180deg,#e9e3cf,#8e8c7a 55%,#6f8d8f)"></div></div>
  </div>
</section>

<section class="abs testimonials">
  <h2 class="abs h2" style="left:132px;top:43px;font-size:22px">Customer<br>Testimonials</h2>
  <div class="abs" style="left:136px;top:170px;font-size:22px;color:#555">&#8249;</div>
  <div class="abs view-all" style="left:170px;top:174px">VIEW ALL</div>
  <div class="abs" style="left:270px;top:170px;font-size:22px;color:#555">&#8250;</div>

  <div class="quote" style="left:387px">Contrary to popular belief, Lorem Ipsum is not simply random text. It has roots in a piece of classical Latin literature from 45 BC, making it over<div class="stars">&#9733;&#9733;&#9733;&#9733;&#9733;</div><div class="who">OWEN, England</div></div>
  <div class="divider" style="left:597px"></div>
  <div class="quote" style="left:646px">Contrary to popular belief, Lorem Ipsum is not simply random text. It has roots in a piece of classical Latin literature from 45 BC, making it over<div class="stars">&#9733;&#9733;&#9733;&#9733;&#9733;</div><div class="who">OWEN, England</div></div>
  <div class="divider" style="left:852px"></div>
  <div class="quote" style="left:910px">Contrary to popular belief, Lorem Ipsum is not simply random text. It has roots in a piece of classical Latin literature from 45 BC, making it over<div class="stars">&#9733;&#9733;&#9733;&#9733;&#9733;</div><div class="who">OWEN, England</div></div>
</section>

<footer class="abs footer">
  <div class="abs foot-brand"><div class="brand-dot"></div><div class="brand-name">BRINDLE HARBOR</div><div class="brand-sub">STUDIOS</div></div>
  <div class="abs menu-label">MENU</div>
  <div class="abs address">42 Larchmere Lane,<br>Eastholm,<br>Fernshire, Scotland,<br>FH3 7QD</div>
  <div class="abs map" role="img" aria-label="Street map showing the studio location">
    <svg width="387" height="273" viewBox="0 0 387 273" style="position:absolute;left:0;top:0"><path d="M172 60c-6 0-10 5-10 11 0 8 10 18 10 18s10-10 10-18c0-6-4-11-10-11z" fill="#d9362b"/><circle cx="172" cy="71" r="3.5" fill="#fff"/></svg>
  </div>
  <div class="abs news-label">NEWSLETTER SIGNUP!</div>
  <div class="abs news">
    <div class="news-field"><svg width="12" height="9" viewBox="0 0 12 9"><rect x=".5" y=".5" width="11" height="8" fill="none" stroke="#777"/><path d="M.5.5l5.5 4 5.5-4" stroke="#777" fill="none"/></svg>E mail id</div>
    <div class="news-btn">SIGNUP</div>
  </div>
  <div class="abs foot-line"></div>
  <div class="abs follow">FOLLOW US
    <div class="social"><span style="background:#3b5bab"></span><span style="background:#2aa3e0"></span><span style="background:#d8493a"></span></div>
  </div>
  <div class="abs links">My Account &nbsp;| &nbsp;Wishlist &nbsp;| &nbsp;FAQ &nbsp;| &nbsp;My Cart &nbsp;| &nbsp;Payment Options &nbsp;| &nbsp;Terms &amp; Condition</div>
  <div class="abs copy">Copyrights @ 2017 All Rights Reserved</div>
</footer>

</body>
</html>
```